Business cards to launch an education platform

Hi,
I am looking at having new business cards designed.
I am a startup, developing a web platform for schools and university, the education world. It's an online assessment system.
I would like a card that looks classy, and that is using the colors and the font of my logo.

I have attached:
1) my logo
2) A business card that I have designed quickly so you can have all the information required in the card, but I really don't like it.
3) The font that I am using (Lato Regular) to design my web platform
4) Some screenshots of my web platform so you can have a look at the style that I have.

Target Market(s)

Major market: Education system: Schools and university
Minor markets: Business in general

Industry/Entity Type

Business

Contact Information for Business Card

Clara Fenwick
Director

M: 0437 518 902
E: clara.fenwick@amberLoomSystems.com.au

Requirements
Must have
• The colors of my logo

```html
<!DOCTYPE html>
<html lang="en">
<head>
<meta charset="utf-8">
<title>Amber Loom Systems – Business Cards</title>
<link rel="stylesheet" href="https://fonts.googleapis.com/css2?family=Lato:wght@400;700&display=swap">
<style>
  :root {
    --backdrop: #e9ebee;
    --card-white: #ffffff;
    --card-white-shade: #eef0f2;
    --blue-light: #0a74c8;
    --blue-deep: #06427f;
    --navy-text: #0c3768;
    --cyan: #27c6ea;
    --white: #ffffff;
  }
  * { box-sizing: border-box; margin: 0; padding: 0; }
  html, body {
    width: 1200px;
    height: 900px;
    overflow: hidden;
    background: var(--backdrop);
    font-family: "Lato", sans-serif;
  }
  .canvas { position: relative; width: 1200px; height: 900px; }

  .card {
    position: absolute;
    width: 620px;
    height: 354px;
    border-radius: 4px;
    overflow: hidden;
    box-shadow: 0 12px 30px rgba(0, 0, 0, 0.18);
  }

  /* Back of card */
  .card--back {
    left: 110px;
    top: 80px;
    background: linear-gradient(180deg, var(--blue-light) 0%, var(--blue-deep) 100%);
  }
  .card--back .brand {
    position: absolute;
    left: 0;
    right: 0;
    top: 126px;
    display: flex;
    justify-content: center;
    align-items: center;
  }

  /* Brand lockup */
  .brand__name {
    text-align: right;
    font-weight: 400;
    letter-spacing: 0.14em;
    line-height: 1.15;
  }
  .brand__line-1 { display: block; font-size: 31px; }
  .brand__line-2 { display: block; font-size: 19px; }
  .brand__divider {
    width: 2px;
    height: 96px;
    margin: 0 22px;
  }
  .brand__mark {
    width: 62px;
    height: 62px;
  }
  .card--back .brand__name { color: var(--white); }
  .card--back .brand__divider { background: var(--white); }
  .card--back .brand__mark { background: var(--white); }

  /* Front of card */
  .card--front {
    left: 470px;
    top: 470px;
    background: linear-gradient(180deg, var(--card-white) 0%, var(--card-white-shade) 100%);
  }
  .card--front .brand {
    position: absolute;
    left: 110px;
    top: 38px;
    display: flex;
    align-items: center;
  }
  .card--front .brand__name { color: var(--navy-text); }
  .card--front .brand__divider { background: var(--cyan); width: 1.5px; }
  .card--front .brand__mark { background: var(--blue-light); }

  .stripe {
    position: absolute;
    left: 0;
    right: 0;
    top: 166px;
    height: 9px;
    background: var(--cyan);
  }
  .band {
    position: absolute;
    left: 0;
    right: 0;
    top: 182px;
    bottom: 0;
    background: linear-gradient(180deg, var(--blue-light) 0%, var(--blue-deep) 100%);
    color: var(--white);
  }
  .contact {
    position: absolute;
    right: 190px;
    top: 22px;
    text-align: right;
    font-size: 14px;
    line-height: 22px;
  }
  .contact__row { display: flex; justify-content: flex-end; align-items: center; gap: 8px; }
  .contact__icon { width: 12px; height: 12px; fill: var(--white); }
  .person {
    position: absolute;
    left: 452px;
    top: 16px;
  }
  .person__name { font-size: 18px; font-weight: 700; }
  .person__role { font-size: 12px; margin-top: 4px; }
  .email-large {
    position: absolute;
    left: 28px;
    bottom: 30px;
    font-size: 17px;
    letter-spacing: 0.01em;
  }
</style>
</head>
<body>
<main class="canvas">

  <section class="card card--back" aria-label="Business card back">
    <div class="brand">
      <p class="brand__name">
        <span class="brand__line-1">AMBER</span>
        <span class="brand__line-2">Loom Systems</span>
      </p>
      <span class="brand__divider"></span>
      <span class="brand__mark"></span>
    </div>
  </section>

  <section class="card card--front" aria-label="Business card front">
    <div class="brand">
      <p class="brand__name">
        <span class="brand__line-1">AMBER</span>
        <span class="brand__line-2">Loom Systems</span>
      </p>
      <span class="brand__divider"></span>
      <span class="brand__mark"></span>
    </div>

    <div class="stripe"></div>

    <div class="band">
      <div class="contact">
        <p class="contact__row">0437 518 902
          <svg class="contact__icon" viewBox="0 0 24 24" aria-hidden="true"><path d="M6.6 10.8a15.1 15.1 0 0 0 6.6 6.6l2.2-2.2a1 1 0 0 1 1-.25 11.4 11.4 0 0 0 3.6.57 1 1 0 0 1 1 1V20a1 1 0 0 1-1 1A17 17 0 0 1 3 4a1 1 0 0 1 1-1h3.5a1 1 0 0 1 1 1c0 1.25.2 2.45.57 3.6a1 1 0 0 1-.25 1z"/></svg>
        </p>
        <p class="contact__row">amberLoomSystems.com.au
          <svg class="contact__icon" viewBox="0 0 24 24" aria-hidden="true"><path d="M2 5h20v14H2z M3.5 6.5 12 13l8.5-6.5" fill="none" stroke="#ffffff" stroke-width="2"/></svg>
        </p>
      </div>
      <div class="person">
        <p class="person__name">Clara Fenwick</p>
        <p class="person__role">Director</p>
      </div>
      <p class="email-large">clara.fenwick@amberLoomSystems.com.au</p>
    </div>
  </section>

</main>
</body>
</html>
```